Business Card Design Project

Business card based on attached logo

Todd Merrick
Todd@lorvantest.com
877-514-9073 ext. 318
Www.LorvanTest.com

Industry/Entity Type

Business

```html
<!DOCTYPE html>
<html lang="en">
<head>
<meta charset="utf-8">
<title>LorvanTest Business Cards</title>
<link href="https://fonts.googleapis.com/css2?family=Jost:wght@400;500;700&display=swap" rel="stylesheet">
<style>
  :root {
    --brand-red: #ec1c24;
    --ink: #231f20;
    --paper: #ffffff;
    --table: #7a4220;
    --muted: #8a8a8a;
  }
  * { margin: 0; padding: 0; box-sizing: border-box; }
  html, body {
    width: 1200px;
    height: 716px;
    overflow: hidden;
  }
  body {
    position: relative;
    background: var(--table);
    font-family: "Jost", "Futura", sans-serif;
  }
  .card {
    position: absolute;
    width: 507px;
    height: 289px;
    overflow: hidden;
    box-shadow: 0 2px 6px rgba(0, 0, 0, 0.35);
  }
  .card--front  { left: 52px;  top: 36px;  background: var(--paper); }
  .card--white  { left: 623px; top: 36px;  background: var(--paper); }
  .card--red    { left: 48px;  top: 379px; background: var(--brand-red); }
  .card--black  { left: 628px; top: 381px; background: var(--ink); }

  /* Front card */
  .front-wave {
    position: absolute;
    inset: 0;
    width: 100%;
    height: 100%;
  }
  .brand-lockup {
    position: absolute;
    left: 50px;
    top: 98px;
    display: flex;
    align-items: center;
    gap: 10px;
  }
  .brand-lockup__name {
    font-weight: 700;
    font-size: 30px;
    letter-spacing: 0.5px;
    color: var(--ink);
  }
  .brand-lockup__square {
    width: 18px;
    height: 18px;
    background: var(--brand-red);
  }
  .divider {
    position: absolute;
    left: 272px;
    top: 62px;
    width: 1px;
    height: 108px;
    background: linear-gradient(to bottom, transparent, #b5b5b5 20%, #b5b5b5 80%, transparent);
  }
  .contact {
    position: absolute;
    left: 287px;
    top: 68px;
  }
  .contact__name {
    font-weight: 700;
    font-size: 20px;
    letter-spacing: 1px;
    color: var(--brand-red);
    margin-bottom: 14px;
  }
  .contact__line {
    display: flex;
    align-items: center;
    gap: 6px;
    font-size: 14px;
    color: var(--ink);
    margin-bottom: 6px;
  }
  .contact__icon {
    width: 10px;
    height: 10px;
    fill: var(--brand-red);
  }
  .front-url {
    position: absolute;
    left: 0;
    right: 0;
    bottom: 8px;
    text-align: center;
    font-weight: 700;
    font-size: 13px;
    letter-spacing: 2px;
    color: var(--paper);
  }

  /* Back cards */
  .back-mark {
    position: absolute;
    left: 0;
    right: 0;
    top: 112px;
    display: flex;
    justify-content: center;
    align-items: center;
    gap: 14px;
  }
  .back-mark__name {
    font-weight: 700;
    font-size: 46px;
    letter-spacing: 0.5px;
  }
  .back-mark__square {
    width: 34px;
    height: 34px;
  }
  .back-url {
    position: absolute;
    left: 0;
    right: 0;
    top: 262px;
    text-align: center;
    font-weight: 400;
    font-size: 15px;
    letter-spacing: 2.6px;
  }
  .card--white .back-mark__name   { color: var(--brand-red); }
  .card--white .back-mark__square { background: var(--brand-red); }
  .card--white .back-url          { color: var(--ink); top: 262px; }
  .card--red .back-mark__name,
  .card--black .back-mark__name   { color: var(--paper); }
  .card--red .back-mark__square,
  .card--black .back-mark__square { background: var(--paper); }
  .card--red .back-url,
  .card--black .back-url          { color: var(--paper); top: 262px; }
</style>
</head>
<body>

  <section class="card card--front">
    <svg class="front-wave" viewBox="0 0 507 289" preserveAspectRatio="none" aria-hidden="true">
      <path d="M0,216 C110,268 200,272 280,250 C360,228 440,212 507,214 L507,289 L0,289 Z" fill="var(--brand-red)"/>
      <path d="M0,216 C110,264 200,266 280,244 C360,222 440,208 507,208 L507,214 C440,212 360,228 280,250 C200,272 110,268 0,220 Z" fill="var(--paper)"/>
      <path d="M0,212 C110,258 200,258 280,236 C360,214 440,204 507,206 L507,210 C440,208 360,220 280,242 C200,262 110,262 0,216 Z" fill="var(--ink)"/>
    </svg>

    <div class="brand-lockup">
      <span class="brand-lockup__name">LorvanTest</span>
      <span class="brand-lockup__square"></span>
    </div>

    <div class="divider"></div>

    <div class="contact">
      <p class="contact__name">Todd Merrick</p>
      <p class="contact__line">
        <svg class="contact__icon" viewBox="0 0 10 10" aria-hidden="true"><path d="M2,0.5 L3.8,2.6 L2.8,3.8 C3.4,5.2 4.8,6.6 6.2,7.2 L7.4,6.2 L9.5,8 L8.2,9.5 C4.2,9 1,5.8 0.5,1.8 Z"/></svg>
        877-514-9073 ext. 318
      </p>
      <p class="contact__line">
        <svg class="contact__icon" viewBox="0 0 10 10" aria-hidden="true"><path d="M0.5,2.5 L9.5,2.5 L9.5,8.5 L0.5,8.5 Z M0.5,2.5 L5,6 L9.5,2.5" stroke="var(--paper)" stroke-width="0.8"/></svg>
        Todd@lorvantest.com
      </p>
    </div>

    <p class="front-url">www.LorvanTest.com</p>
  </section>

  <section class="card card--white">
    <div class="back-mark">
      <span class="back-mark__name">LorvanTest</span>
      <span class="back-mark__square"></span>
    </div>
    <p class="back-url">www.LorvanTest.com</p>
  </section>

  <section class="card card--red">
    <div class="back-mark">
      <span class="back-mark__name">LorvanTest</span>
      <span class="back-mark__square"></span>
    </div>
    <p class="back-url">www.LorvanTest.com</p>
  </section>

  <section class="card card--black">
    <div class="back-mark">
      <span class="back-mark__name">LorvanTest</span>
      <span class="back-mark__square"></span>
    </div>
    <p class="back-url">www.LorvanTest.com</p>
  </section>

</body>
</html>
```